Brenlow Estates Website and Logo Design

We need a new logo and website designed for 'Brenlow Estates Ltd', which is a well established Guernsey property holding company founded in 1934.

The company does not currently have a website. The new website should be similar in style and layout to https://www.quorvanhall.example/.

Target Market(s)

Industry, Media, Tenants

Industry/Entity Type

Property Management

Logo Text

BEL OR Brenlow Estates Ltd OR BE

Coding

Coded - Design and coding required

Number of Pages Required

4 page

Font styles to use
Other font styles liked:
• Helvetica

Requirements
Must have
• The logo laying over the picture (like https://www.quorvanhall.example/).
• Big pictures on homepage (like https://www.quorvanhall.example/)

```html
<!DOCTYPE html>
<html lang="en">
<head>
<meta charset="utf-8">
<title>Brenlow Estates Limited</title>
<link rel="stylesheet" href="https://fonts.googleapis.com/css2?family=Roboto+Condensed:wght@400;700&family=Open+Sans:ital,wght@0,400;0,600;1,400;1,600&family=Roboto:wght@400;500&display=swap">
<style>
:root{
  --blue:#1e87c2;
  --blue-dark:#1a78ad;
  --green:#7ab72f;
  --green-light:#8cc63f;
  --ink:#2b2b2b;
  --text:#555;
  --muted:#777;
  --line:#e3e3e3;
  --white:#fff;
}
*{margin:0;padding:0;box-sizing:border-box}
html,body{width:1200px;height:2889px;overflow:hidden}
body{position:relative;background:var(--white);font-family:'Open Sans',Arial,sans-serif;color:var(--text)}
h1,h2,h3,h4,h5{font-weight:400}
.section{position:absolute;left:0;width:1200px}
.abs{position:absolute}

/* hero */
.hero{top:0;height:595px;background:linear-gradient(180deg,#1d2a40 0%,#34465c 30%,#54606a 48%,#2d3c4a 62%,#1b2836 100%);overflow:hidden}
.hero-shade{position:absolute;inset:0;background:rgba(10,20,35,.25)}
.logo{left:100px;top:32px;color:var(--white);font-family:'Roboto Condensed',Arial,sans-serif;font-weight:700;line-height:1}
.logo .name{font-size:44px;letter-spacing:.5px}
.logo .sub{font-size:19px;margin-top:2px;padding-left:4px}
.nav{right:60px;top:50px;display:flex;align-items:center;gap:30px;font-family:'Roboto',Arial,sans-serif;font-size:12px;font-weight:500;color:var(--white);text-transform:uppercase}
.nav .active{background:var(--green-light);padding:6px 20px;border-radius:12px}
.hero-title{left:0;width:1200px;top:338px;text-align:center;color:var(--white);font-family:'Roboto Condensed',Arial,sans-serif;font-weight:700;font-size:50px;text-shadow:0 2px 6px rgba(0,0,0,.5)}
.hero-text{left:290px;width:620px;top:402px;text-align:center;color:var(--white);font-size:14.5px;line-height:26px}
.dots{left:0;width:1200px;top:478px;display:flex;justify-content:center;gap:8px}
.dots span{width:11px;height:11px;border-radius:50%;background:var(--white)}
.dots .on{background:transparent;border:2px solid var(--white);width:17px;height:17px;margin-top:-3px}

/* welcome */
.welcome{top:595px;height:487px}
.section-title{font-family:'Roboto Condensed',Arial,sans-serif;font-size:36px;color:var(--ink);text-align:center;width:1200px;left:0}
.welcome .section-title{top:64px}
.welcome-text{left:132px;width:936px;top:124px;text-align:center;font-size:11px;line-height:21px;color:var(--muted)}
.service{top:233px;width:280px;height:170px;background:var(--white);border:1px solid var(--line);border-bottom:3px solid #cfe3f0;padding:18px 14px 0 48px}
.service h3{font-family:'Roboto',Arial,sans-serif;font-size:17px;color:#444;text-transform:uppercase;margin-bottom:8px;white-space:nowrap}
.service p{font-size:11.5px;line-height:21px;color:#666}
.service .more{font-size:12px;color:#555;margin-top:14px;text-transform:uppercase}
.badge{top:280px;width:72px;height:72px;border-radius:50%;display:flex;align-items:center;justify-content:center}
.badge.blue{background:var(--blue)}
.badge.green{background:var(--green)}

/* why */
.why{top:1082px;height:486px;background:linear-gradient(135deg,#f3f8fc,#e6f0f9 60%,#eef5fb);border-top:1px solid #dde8f2;border-bottom:1px solid #dde8f2}
.video{left:102px;top:86px;width:418px;height:322px;border:4px solid #ddd;background:#111}
.video-bar{height:38px;background:#1c1c1c;color:var(--white);font-size:11px;display:flex;align-items:center;justify-content:space-between;padding:0 12px;text-transform:uppercase}
.video-media{height:276px;background:linear-gradient(180deg,#3b4656 0%,#4e5966 45%,#2a3440 70%,#1b232c 100%);display:flex;align-items:center;justify-content:center}
.play{width:44px;height:30px;background:rgba(255,255,255,.85);border-radius:6px;display:flex;align-items:center;justify-content:center}
.why h2{left:560px;top:110px;font-family:'Roboto Condensed',Arial,sans-serif;font-size:30px;color:#333}
.why-body{left:562px;top:162px;width:576px;font-size:11px;line-height:21px;color:#555}
.why-body p{margin-bottom:10px}

/* listings */
.listings{top:1568px;height:528px}
.listings .section-title{top:68px;font-size:31px;text-transform:uppercase}
.card{top:148px;width:234px;height:304px;background:#fffdf6;border:1px solid #ece6d4}
.card-photo{height:172px;margin:2px}
.card p{padding:10px 12px 0 12px;font-size:11.5px;line-height:21px;color:#555;height:84px}
.card-foot{position:absolute;left:0;right:0;bottom:0;height:44px;border-top:1px solid #ece6d4;display:flex;font-size:11.5px;color:#444}
.card-foot .place{flex:1;display:flex;align-items:center;gap:7px;padding-left:12px;border-right:1px solid #ece6d4}
.card-foot .price{width:72px;display:flex;align-items:center;justify-content:center}

/* news */
.news{top:2096px;height:437px;background:linear-gradient(135deg,#f4f4f4,#ececec 50%,#f2f2f2)}
.block-title{font-family:'Roboto',Arial,sans-serif;font-size:27px;color:#333;text-transform:uppercase}
.article{top:140px;width:300px}
.article h4{font-family:'Roboto',Arial,sans-serif;font-size:18px;color:#333}
.article .date{font-weight:600;font-style:italic;color:var(--green);font-size:16px;margin-top:10px}
.article p{font-size:12px;line-height:22px;color:#666;margin-top:10px}
.article .more{font-size:12px;color:#444;margin-top:20px;display:flex;align-items:center;gap:6px;text-transform:uppercase}
.article .rule{height:1px;background:#dcdcdc;margin-top:14px}
.quote{left:784px;top:120px;width:318px;height:183px;background:var(--green);color:var(--white);font-style:italic;font-size:11.5px;line-height:21px;padding:20px 24px}
.quote .who{font-weight:600;padding-left:120px;margin-top:8px;line-height:20px}
.avatar{left:806px;top:306px;width:84px;height:84px;border-radius:50%;border:4px solid var(--white);background:linear-gradient(160deg,#c9a98c,#7d6a5c)}

/* footer */
.footer{top:2533px;height:356px;background:var(--blue)}
.grass{top:0;height:10px;width:1200px;left:0;background:linear-gradient(180deg,var(--green-light),#6ea82d)}
.flogo{left:98px;top:60px;color:var(--white);font-family:'Roboto Condensed',Arial,sans-serif;font-weight:700;line-height:1}
.flogo .name{font-size:44px}
.flogo .sub{font-size:19px;margin-top:2px;padding-left:4px}
.social{left:98px;top:160px;color:var(--white);font-size:14px}
.social .row{display:flex;gap:16px;margin-bottom:10px}
.social span{display:flex;align-items:center;gap:8px}
.social i{display:inline-block;width:26px;height:26px;border:2px solid var(--white);border-radius:50%}
.fcol h5{font-family:'Roboto',Arial,sans-serif;font-weight:500;font-size:16px;color:var(--white);text-transform:uppercase;margin-bottom:18px}
.fcol{color:var(--white);font-size:12.5px;line-height:21px}
.input{width:225px;height:40px;background:var(--white);color:#666;font-size:11px;padding:12px 14px;margin-top:16px}
.btn{display:inline-block;background:var(--green);color:var(--white);font-size:12px;padding:10px 18px;margin-top:14px;text-transform:uppercase}
.contact-line{display:flex;align-items:center;gap:14px;margin-top:14px}
.links li{list-style:none;display:flex;align-items:center;gap:10px;line-height:22px}
.links li::before{content:"";border-left:5px solid var(--white);border-top:4px solid transparent;border-bottom:4px solid transparent}
.copyright{left:0;top:293px;width:1200px;height:63px;background:var(--blue-dark);border-top:1px solid rgba(255,255,255,.15);color:var(--white);font-size:12px;text-align:center;line-height:63px}
</style>
</head>
<body>

<header class="section hero">
  <div class="abs" style="inset:0" role="img" aria-label="Harbour photograph with moored boats and waterfront town buildings"></div>
  <div class="hero-shade"></div>
  <div class="abs logo"><div class="name">BRENLOW</div><div class="sub">Estates Limited</div></div>
  <nav class="abs nav">
    <span class="active">Home</span><span>About Us</span><span>Services</span><span>Projects</span><span>Contact Us</span>
    <svg width="13" height="13" viewBox="0 0 13 13"><circle cx="5" cy="5" r="4" fill="none" stroke="#fff" stroke-width="2"/><line x1="8" y1="8" x2="12" y2="12" stroke="#fff" stroke-width="2"/></svg>
  </nav>
  <h1 class="abs hero-title">BRENLOW ESTATES LIMITED</h1>
  <p class="abs hero-text">Brenlow Estates Limited (BEL) is a family-owned Guernsey property holding company. It purchases properties that are considered to have potential</p>
  <div class="abs dots"><span class="on"></span><span></span><span></span><span></span></div>
</header>

<section class="section welcome">
  <h2 class="abs section-title">Welcome To Brenlow Estates Limited</h2>
  <p class="abs welcome-text">Brenlow Estates Limited (BEL) is a family-owned Guernsey property holding company. It purchases properties that are considered to have potential for development either through refurbishment or by obtaining planning permission to change its classification from, for example, industrial premises to offices or retail outlets, or by the marriage value of buying an adjacent property to one already owned by BEL. BEL's reputation as a fair-minded landlord stems from the application of the founder's tenet of working</p>

  <div class="abs service" style="left:135px"><h3>Property Management</h3><p>Lorem ipsum dolor sit amet, consetetur adipiscing elit, sed do eiusmod tempor incididunt ut labore et dolore</p><div class="more">Read More</div></div>
  <div class="abs badge blue" style="left:100px"><svg width="36" height="34" viewBox="0 0 36 34"><path d="M18 2 L34 16 H29 V32 H7 V16 H2 Z" fill="#fff"/><circle cx="18" cy="22" r="5" fill="none" stroke="#1e87c2" stroke-width="2"/></svg></div>

  <div class="abs service" style="left:478px"><h3>Property Rentals</h3><p>Lorem ipsum dolor sit amet, consetetur adipiscing elit, sed do eiusmod tempor incididunt ut labore et dolore</p><div class="more">Read More</div></div>
  <div class="abs badge green" style="left:443px"><svg width="36" height="34" viewBox="0 0 36 34"><path d="M18 2 L34 16 H29 V32 H7 V16 H2 Z" fill="#fff"/><rect x="14" y="20" width="8" height="12" fill="#7ab72f"/></svg></div>

  <div class="abs service" style="left:820px"><h3>How Can Help You?</h3><p>Lorem ipsum dolor sit amet, consetetur adipiscing elit, sed do eiusmod tempor incididunt ut labore et dolore</p><div class="more">Read More</div></div>
  <div class="abs badge blue" style="left:785px"><svg width="36" height="36" viewBox="0 0 36 36"><circle cx="18" cy="18" r="14" fill="none" stroke="#fff" stroke-width="6"/><circle cx="18" cy="18" r="14" fill="none" stroke="#1e87c2" stroke-width="6" stroke-dasharray="10 12"/></svg></div>
</section>

<section class="section why">
  <div class="abs video">
    <div class="video-bar"><span>The Harbour Lending Institute......</span>
      <svg width="40" height="14" viewBox="0 0 40 14"><circle cx="7" cy="7" r="6" fill="none" stroke="#fff" stroke-width="2"/><line x1="7" y1="7" x2="7" y2="3" stroke="#fff" stroke-width="2"/><circle cx="30" cy="7" r="2.5" fill="#fff"/><circle cx="37" cy="3" r="2.5" fill="#fff"/><circle cx="37" cy="11" r="2.5" fill="#fff"/><path d="M30 7 L37 3 M30 7 L37 11" stroke="#fff" stroke-width="1.5"/></svg>
    </div>
    <div class="video-media" role="img" aria-label="Video still of the harbour town at dusk with boats">
      <div class="play"><svg width="14" height="14" viewBox="0 0 14 14"><path d="M2 1 L13 7 L2 13 Z" fill="#333"/></svg></div>
    </div>
  </div>
  <h2 class="abs">WHY GUERNSEY?</h2>
  <div class="abs why-body">
    <p>The Bailiwick of Guernsey is a British Crown dependency in the English Channel. The benefit of establishing a company in Guernsey is the island's low tax jurisdiction since there are no capital taxes and no corporation taxes for many companies. Consequently since the 1980s the island's development as an ideal financial centre for the establishment of institutions and banks has thrived.</p>
    <p>There are currently more than 160 companies registered with the Island Business Registry Board (28 banks, building societies, stock brokerage and asset management firms, insurance and finance companies, retailers and credit unions are the basic types of financial institutions) and it is this group of financial institutions that is the greatest generator of tax revenue. Many Guernsey-registered companies have a policy of renting property rather than purchasing. Most prefer to put their capital into the business and not into property whilst others simply cannot afford the large capital outlay required to buy. Their view, often, is that they are not property experts and leave that métier to specialist companies such as Brenlow Estates Limited.</p>
  </div>
</section>

<section class="section listings">
  <h2 class="abs section-title">Properties Listings</h2>
  <div class="abs card" style="left:102px"><div class="card-photo" role="img" aria-label="Two-storey family house with porch and lawn" style="background:linear-gradient(180deg,#8fb8e0 0%,#c9d7e2 40%,#9c8d7a 60%,#6f9a3e 85%)"></div><p>Lorem ipsum dolor sit amet, consetur adipiscing elit, sed do eiusmod tempor incididunt ut labore et</p><div class="card-foot"><span class="place"><svg width="8" height="11" viewBox="0 0 8 11"><path d="M4 0 A4 4 0 0 1 8 4 C8 7 4 11 4 11 C4 11 0 7 0 4 A4 4 0 0 1 4 0Z" fill="#555"/><circle cx="4" cy="4" r="1.5" fill="#fffdf6"/></svg>Los Angeles, California</span><span class="price">$370,000</span></div></div>
  <div class="abs card" style="left:358px"><div class="card-photo" role="img" aria-label="Modern house lit at dusk beside a pool" style="background:linear-gradient(180deg,#1d2333 0%,#4a4236 45%,#c79a58 62%,#2c6f8f 85%)"></div><p>Lorem ipsum dolor sit amet, consetur adipiscing elit, sed do eiusmod tempor incididunt ut labore et</p><div class="card-foot"><span class="place"><svg width="8" height="11" viewBox="0 0 8 11"><path d="M4 0 A4 4 0 0 1 8 4 C8 7 4 11 4 11 C4 11 0 7 0 4 A4 4 0 0 1 4 0Z" fill="#555"/><circle cx="4" cy="4" r="1.5" fill="#fffdf6"/></svg>Los Angeles, California</span><span class="price">$370,000</span></div></div>
  <div class="abs card" style="left:614px"><div class="card-photo" role="img" aria-label="White contemporary house with blue glazing" style="background:linear-gradient(180deg,#3d7fc2 0%,#9bc2e6 40%,#e9eef2 60%,#7f95a8 100%)"></div><p>Lorem ipsum dolor sit amet, consetur adipiscing elit, sed do eiusmod tempor incididunt ut labore et</p><div class="card-foot"><span class="place"><svg width="8" height="11" viewBox="0 0 8 11"><path d="M4 0 A4 4 0 0 1 8 4 C8 7 4 11 4 11 C4 11 0 7 0 4 A4 4 0 0 1 4 0Z" fill="#555"/><circle cx="4" cy="4" r="1.5" fill="#fffdf6"/></svg>Los Angeles, California</span><span class="price">$370,000</span></div></div>
  <div class="abs card" style="left:870px"><div class="card-photo" role="img" aria-label="Villa with palm trees and pool at sunset" style="background:linear-gradient(180deg,#2f4d78 0%,#8a7f85 40%,#e0c9a6 62%,#3b6f87 88%)"></div><p>Lorem ipsum dolor sit amet, consetur adipiscing elit, sed do eiusmod tempor incididunt ut labore et</p><div class="card-foot"><span class="place"><svg width="8" height="11" viewBox="0 0 8 11"><path d="M4 0 A4 4 0 0 1 8 4 C8 7 4 11 4 11 C4 11 0 7 0 4 A4 4 0 0 1 4 0Z" fill="#555"/><circle cx="4" cy="4" r="1.5" fill="#fffdf6"/></svg>Los Angeles, California</span><span class="price">$370,000</span></div></div>
</section>

<section class="section news">
  <h2 class="abs block-title" style="left:98px;top:68px">Latest News</h2>
  <article class="abs article" style="left:98px"><h4>Nemo Enim Ipsam Voluptatem ?</h4><div class="date">Janu 21, 2016</div><p>Duis aute irure dolor in reprehenderit in voluptate velit esse cillum dolore eu fugiat nulla pariatur. Excepteur sint occaecat cupidatat non proident, sunt in culpa qui officia deserunt mollit</p><div class="more"><svg width="11" height="11" viewBox="0 0 11 11"><circle cx="5.5" cy="5.5" r="4.5" fill="none" stroke="#444" stroke-width="1.5"/><path d="M5.5 3 V5.5 H7.5" stroke="#444" stroke-width="1.3" fill="none"/></svg>Read More</div><div class="rule"></div></article>
  <article class="abs article" style="left:447px"><h4>Nemo Enim Ipsam Voluptatem ?</h4><div class="date">Janu 21, 2016</div><p>Duis aute irure dolor in reprehenderit in voluptate velit esse cillum dolore eu fugiat nulla pariatur. Excepteur sint occaecat cupidatat non proident, sunt in culpa qui officia deserunt mollit</p><div class="more"><svg width="11" height="11" viewBox="0 0 11 11"><circle cx="5.5" cy="5.5" r="4.5" fill="none" stroke="#444" stroke-width="1.5"/><path d="M5.5 3 V5.5 H7.5" stroke="#444" stroke-width="1.3" fill="none"/></svg>Read More</div><div class="rule"></div></article>
  <h2 class="abs block-title" style="left:784px;top:70px">Testimonial</h2>
  <blockquote class="abs quote">" Duis aute irure dolor in reprehenderit in voluptate velit esse cillum dolore eu fugiat nulla pariatur. Excepteur sint occaecat cupidatat non proident, sunt in culpa qui officia deserunt mollit anim id est laborum."<div class="who">- MAREN TOLLIS<br>Property Agent ,</div></blockquote>
  <div class="abs avatar" role="img" aria-label="Portrait photo of the property agent"></div>
</section>

<footer class="section footer">
  <div class="abs grass"></div>
  <div class="abs flogo"><div class="name">BRENLOW</div><div class="sub">Estates Limited</div></div>
  <div class="abs social">
    <div class="row"><span><i></i>Community</span><span><i></i>Network</span></div>
    <div class="row"><span><i></i>Updates</span></div>
  </div>
  <div class="abs fcol" style="left:370px;top:60px;width:240px">
    <h5>Sign Up For Newsletter</h5>
    <div>Excepteur sint occaecat cupidatat non proident, sunt in culpa qui</div>
    <div class="input">Enter Name</div>
    <div class="btn">Subscribe</div>
  </div>
  <div class="abs fcol" style="left:664px;top:62px;width:280px">
    <h5>Contact Us</h5>
    <div>Brenlow Estates Limited<br>Unit 12, 48 Quayside Row<br>St Peter Port, GY1 4QX</div>
    <div class="contact-line"><svg width="16" height="16" viewBox="0 0 16 16"><path d="M3 1 L6 1 L7 5 L5 6.5 C6 9 7 10 9.5 11 L11 9 L15 10 L15 13 C15 14 14 15 13 15 C6 15 1 10 1 3 C1 2 2 1 3 1Z" fill="none" stroke="#fff" stroke-width="1.3"/></svg>555.014.2270 (Tel)</div>
    <div class="contact-line"><svg width="16" height="12" viewBox="0 0 16 12"><rect x="1" y="1" width="14" height="10" fill="none" stroke="#fff" stroke-width="1.3"/><path d="M1 1 L8 7 L15 1" fill="none" stroke="#fff" stroke-width="1.3"/></svg>Email: info@BrenlowEstates.com</div>
  </div>
  <div class="abs fcol" style="left:976px;top:60px;width:180px">
    <h5>Quick Links</h5>
    <ul class="links"><li>Home</li><li>About Us</li><li>Brenlow Estates</li><li>Services</li><li>Blog</li><li>Contact</li></ul>
  </div>
  <div class="abs copyright">2016 © Copyrights Brenlow Estates Limited.All Rights Reserved</div>
</footer>

</body>
</html>
```